Marwick Law Letterhead

We need a new letterhead design for a Law Firm. The address for the law firm is 1475 Calloway Street, Suite 210, Houston, Texas 77041. Phone Number: 832-361-9027; Fax Number: 832-614-7359. The logo is uploaded to the project.

```html
<!DOCTYPE html>
<html lang="en">
<head>
<meta charset="utf-8">
<title>Marwick Law Letterhead</title>
<link href="https://fonts.googleapis.com/css2?family=Montserrat:wght@400;500;600&display=swap" rel="stylesheet">
<style>
  :root {
    --backdrop: #e8e8e8;
    --paper: #ffffff;
    --red: #d71d2a;
    --red-deep: #6d0712;
    --navy: #1e3667;
    --navy-deep: #152a52;
    --ink: #333333;
    --ink-dark: #1f1f1f;
  }
  * { box-sizing: border-box; margin: 0; padding: 0; }
  html, body {
    width: 1154px; height: 1200px; overflow: hidden;
    background: var(--backdrop);
    font-family: "Montserrat", sans-serif;
  }
  .letterhead {
    position: absolute; left: 162px; top: 20px;
    width: 830px; height: 1160px;
    background: var(--paper);
    box-shadow: 0 6px 24px rgba(0,0,0,0.18);
    overflow: hidden;
  }
  .header-band { position: absolute; left: 0; top: 0; width: 830px; height: 190px; }
  .brand {
    position: absolute; left: 33px; top: 70px;
    display: flex; align-items: center; gap: 12px;
  }
  .brand-mark { width: 30px; height: 30px; border-radius: 50%; background: var(--navy); }
  .brand-name {
    font-size: 30px; font-weight: 600; color: var(--navy); letter-spacing: 0.5px;
  }
  .contact {
    position: absolute; left: 631px; top: 38px;
    color: #fff; font-size: 14px; line-height: 18px;
  }
  .contact-address { margin-bottom: 9px; }
  .contact-line { display: flex; align-items: center; gap: 9px; line-height: 21px; }
  .contact-line svg { width: 12px; height: 12px; }
  .recipient {
    position: absolute; left: 31px; top: 277px;
    font-size: 13.5px; line-height: 20.6px; color: var(--ink-dark);
  }
  .letter-body {
    position: absolute; left: 33px; top: 364px; width: 769px;
    font-size: 13.6px; line-height: 20.6px; color: var(--ink);
    text-align: justify;
  }
  .letter-body p { margin-bottom: 20.6px; }
  .closing {
    position: absolute; left: 31px; top: 946px;
    font-size: 16px; color: var(--ink-dark);
  }
  .signature {
    position: absolute; left: 31px; top: 978px; width: 94px; height: 26px;
    background: linear-gradient(90deg, #d9d9d9, #efefef);
    border-radius: 3px;
  }
  .footer-band { position: absolute; left: 0; top: 1078px; width: 830px; height: 49px; }
  .web {
    position: absolute; left: 502px; top: 1092px;
    display: flex; align-items: center; gap: 7px;
    color: #fff; font-size: 13.5px;
  }
  .web svg { width: 12px; height: 12px; }
</style>
</head>
<body>
<main class="letterhead">
  <svg class="header-band" viewBox="0 0 830 190" aria-hidden="true">
    <defs>
      <linearGradient id="redGrad" x1="0" y1="0" x2="1" y2="0.6">
        <stop offset="0.35" stop-color="#d71d2a"/>
        <stop offset="1" stop-color="#6d0712"/>
      </linearGradient>
    </defs>
    <polygon points="411,0 830,0 830,187 555,187" fill="url(#redGrad)"/>
  </svg>

  <div class="brand">
    <span class="brand-mark"></span>
    <span class="brand-name">Marwick Law</span>
  </div>

  <div class="contact">
    <div class="contact-address">1475 Calloway Street,<br>Suite 210, Houston,<br>Texas 77041</div>
    <div class="contact-line">
      <svg viewBox="0 0 12 12" aria-hidden="true"><path d="M2.5 1 L4.5 1 L5.2 3.6 L3.9 4.6 Q5 7 7.4 8.1 L8.4 6.8 L11 7.5 L11 9.5 Q10.5 11 9 11 Q1 10 1 3 Q1 1.5 2.5 1Z" fill="#fff"/></svg>
      <span>832-361-9027</span>
    </div>
    <div class="contact-line">
      <svg viewBox="0 0 12 12" aria-hidden="true"><rect x="3" y="1" width="6" height="3" fill="#fff"/><rect x="1" y="4.5" width="10" height="4.5" rx="1" fill="#fff"/><rect x="3" y="8" width="6" height="3" fill="#fff"/></svg>
      <span>832-614-7359</span>
    </div>
  </div>

  <div class="recipient">
    Mr/s<br>First Name and Last Name<br>Company Name<br>Address
  </div>

  <div class="letter-body">
    <p>Lorem ipsum dolor sit amet,consectetur adipiscing sed do eiusmod tempor incididunt laboreet dolore magna aliqua.Ut enim ad minim.veniam, quis nostrud exercitation ullamco laboris nisi ut aliquip exea commodo consequat.Lorem ipsum dolor sit amet,consectetur adipiscing sed do eiusmod tempor incididunt.labore et dolore magna aliqua. Ut enim</p>
    <p>Lorem ipsum dolor sit amet, consectetur adipiscing sed do eiusmod tempor incididunt labore et dolore magna aliqua. Ut enim ad minim veniam, quis nostrud exercitation ullamco laboris nisi ut aliquip exea commodo consequat.Duis aute irure dolor in reprehenderit in voluptate velit esse cillum irure dolor in reprehenderit in voluptate velit esse irure</p>
    <p>Lorem ipsum dolor sit amet, consectetur adipiscing sed do eiusmod tempor incididunt labore et dolore magna aliqua. consequat. Duis aute irure dolor in.reprehenderit in voluptate velit esse cillum dolore eu fugiat nulla pariatur. Excepteur sint occaecat cupidatat non proident, sunt in culpa qui officia deserunt mollit,</p>
    <p>Lorem ipsum dolor sit amet, consectetur adipiscing sed do eiusmod tempor incididunt labore et dolore magna aliqua. Ut enim Lorem ipsum dolor sit amet, consectetur adipiscing sed do eiusmod tempor incididunt labore et dolore magna aliqua. Ut enim Lorem ipsum aliqua.ipsum</p>
    <p>Lorem ipsum dolor sit amet, consectetur adipiscing sed do eiusmod tempor incididunt labore et dolore magna aliqua. Ut enim ad minim veniam, quis nostrud exercitation ullamco laboris nisi ut aliquip exea commodo consequat.Duis aute irure dolor in reprehenderit in voluptate velit esse cillum irure dolor in reprehenderit in voluptate velit esse irure</p>
    <p>Lorem ipsum dolor sit amet, consectetur adipiscing sed do eiusmod tempor incididunt labore et dolore magna aliqua. Ut enim ad minim veniam, quis nostrud exercitation ullamco laboris nisi ut aliquip exea commodo consequat.Duis aute irure dolor in reprehenderit in voluptate velit esse cillum irure dolor in reprehenderit in voluptate velit esse irure</p>
  </div>

  <div class="closing">Regards</div>
  <div class="signature" role="img" aria-label="Handwritten signature of the sender"></div>

  <svg class="footer-band" viewBox="0 0 830 49" aria-hidden="true">
    <defs>
      <linearGradient id="navyGrad" x1="0" y1="0" x2="1" y2="0">
        <stop offset="0" stop-color="#152a52"/>
        <stop offset="1" stop-color="#1e3667"/>
      </linearGradient>
      <linearGradient id="footRed" x1="0" y1="0" x2="1" y2="0">
        <stop offset="0.3" stop-color="#d71d2a"/>
        <stop offset="1" stop-color="#6d0712"/>
      </linearGradient>
    </defs>
    <polygon points="0,0 489,0 457,49 0,49" fill="url(#navyGrad)"/>
    <polygon points="500,0 693,0 662,49 468,49" fill="url(#footRed)"/>
    <polygon points="705,0 830,0 830,49 673,49" fill="url(#navyGrad)"/>
  </svg>
  <div class="web">
    <svg viewBox="0 0 12 12" aria-hidden="true"><circle cx="6" cy="6" r="5.5" fill="#fff"/><path d="M3 3.5 Q5 4 4.5 6 Q6 7 5 9.5 M8 2.5 Q7 4.5 9 5.5" stroke="#d71d2a" stroke-width="1.2" fill="none"/></svg>
    <span>www.marwicklaw.com</span>
  </div>
</main>
</body>
</html>
```